Up to the Challenge - PPT Template with Splash Slide

We are looking for a PPT template that has 4 slides.
1. Splash slide (Creative, fun, no content, a visual representation of the theme)
2. Section header slide
3. Content Slide
4. Content Slide, another design option
The theme is 'UP to the Challenge'. The design should reflect this theme.
The colors should be in Purple (#864B99), Blue (#0A80C2), and Green (#52B054).

```html
<!DOCTYPE html>
<html lang="en">
<head>
<meta charset="utf-8">
<title>Summit Deck – Presentation Template</title>
<link href="https://fonts.googleapis.com/css2?family=Poppins:wght@300;400;500&display=swap" rel="stylesheet">
<style>
:root{
  --purple:#864B99;
  --blue:#0A80C2;
  --green:#52B054;
  --ink:#222;
  --body:#444;
  --muted:#b5b5b5;
  --page:#ffffff;
  --shadow:rgba(0,0,0,.18);
}
*{box-sizing:border-box;margin:0;padding:0}
html,body{width:806px;height:1200px;overflow:hidden;background:var(--page)}
body{font-family:'Poppins',sans-serif;position:relative}
.slide{position:absolute;width:375px;height:211px;background:#fff;overflow:hidden;box-shadow:0 0 3px var(--shadow)}
.col-l{left:20px}.col-r{left:411px}
.row-1{top:25px}.row-2{top:258px}.row-3{top:491px}.row-4{top:723px}.row-5{top:959px}
.brand{position:absolute;display:flex;align-items:center;gap:3px;font-weight:500;font-size:8px;letter-spacing:.2px;color:var(--ink);white-space:nowrap}
.brand .dot{width:5px;height:5px;border-radius:50%;background:var(--purple)}
.brand.light{color:#fff}
.brand.light .dot{background:#fff}
.brand.top{top:22px;left:266px}
.title{position:absolute;top:24px;left:21px;font-weight:400;font-size:12px;letter-spacing:.4px;color:var(--purple);white-space:nowrap}
.title .accent{color:var(--blue)}
.title.light,.title.light .accent{color:#fff}
.rule{position:absolute;top:41px;left:21px;width:38px;height:1.5px;background:var(--purple)}
.rule.light{background:#fff}
.tab{position:absolute;left:0;top:21px;width:10px;height:19px;background:var(--purple)}
.photo{position:absolute}
.toc-num{position:absolute;font-weight:300;font-size:11px;color:var(--muted)}
.toc-bar{position:absolute;width:.6px;height:26px;background:#ccc}
.toc-item{position:absolute;width:110px}
.toc-item h3{font-weight:500;font-size:5.6px;letter-spacing:.2px;color:var(--purple);margin-bottom:4px}
.toc-item h3.blue{color:var(--blue)}
.toc-item p{font-size:4.6px;line-height:11px;color:var(--body)}
.icon-box{position:absolute;width:23px;height:23px;background:#fff;box-shadow:0 0 3px rgba(0,0,0,.15);display:flex;align-items:center;justify-content:center}
.body-copy{position:absolute;font-size:4.7px;line-height:11.1px;color:var(--body)}
.callout{position:absolute;left:107px;top:149px;width:89px;height:51px;background:var(--purple);color:#fff;text-align:center;padding-top:9px}
.callout h4{font-weight:400;font-size:7.2px;letter-spacing:.3px;margin-bottom:3px}
.callout p{font-size:4.5px;line-height:11px}
.legend{position:absolute;left:333px;width:19px;height:10px;border-radius:0 5px 5px 0}
</style>
</head>
<body>

<!-- Splash 1 -->
<section class="slide col-l row-1">
  <div class="photo" role="img" aria-label="Photo: a finger flipping wooden letter cubes from CHANGE to CHALLENGE on a dark blue backdrop" style="inset:0;background:linear-gradient(135deg,#24435c 0%,#1c3348 55%,#15283a 100%)"></div>
  <div class="brand light" style="top:45px;left:41px;font-size:12px"><span class="dot"></span>SUMMIT DECK</div>
</section>

<!-- Splash 2 -->
<section class="slide col-r row-1">
  <div class="photo" role="img" aria-label="Aerial photo: a team assembling large white puzzle pieces on grey pavement" style="inset:0;background:linear-gradient(135deg,#8a8a86 0%,#77776f 100%)"></div>
  <svg class="photo" style="inset:0" width="375" height="211" viewBox="0 0 375 211" aria-hidden="true">
    <polygon points="0,82 0,68 70,0 84,0" fill="var(--purple)"/>
    <polygon points="0,152 0,140 140,0 152,0" fill="var(--purple)"/>
    <polygon points="20,211 228,0 375,0 375,211" fill="var(--purple)"/>
    <path d="M62,168 a20,20 0 0 0 34,14 L210,66" stroke="var(--purple)" stroke-width="12" fill="none" stroke-linecap="round"/>
  </svg>
  <div class="brand light" style="top:163px;left:222px;font-size:12px"><span class="dot"></span>SUMMIT DECK</div>
</section>

<!-- Table of contents 1 -->
<section class="slide col-l row-2">
  <h2 class="title">TABLE OF <span class="accent">CONTENTS</span></h2>
  <div class="rule"></div>
  <div class="brand top"><span class="dot"></span>SUMMIT DECK</div>

  <div class="toc-num" style="left:21px;top:75px">01</div><div class="toc-bar" style="left:41px;top:72px"></div>
  <div class="toc-item" style="left:51px;top:67px"><h3>LOREM IPSUM DOLOR</h3><p>Lorem ipsum dolor sit amet, consectetur<br>adipiscing elit.</p></div>
  <div class="toc-num" style="left:205px;top:75px">02</div><div class="toc-bar" style="left:225px;top:72px"></div>
  <div class="toc-item" style="left:235px;top:67px"><h3 class="blue">LOREM IPSUM DOLOR</h3><p>Lorem ipsum dolor sit amet, consectetur<br>adipiscing elit.</p></div>

  <div class="toc-num" style="left:20px;top:124px">03</div><div class="toc-bar" style="left:41px;top:121px"></div>
  <div class="toc-item" style="left:51px;top:116px"><h3>LOREM IPSUM DOLOR</h3><p>Lorem ipsum dolor sit amet, consectetur<br>adipiscing elit.</p></div>
  <div class="toc-num" style="left:204px;top:124px">04</div><div class="toc-bar" style="left:225px;top:121px"></div>
  <div class="toc-item" style="left:235px;top:116px"><h3 class="blue">LOREM IPSUM DOLOR</h3><p>Lorem ipsum dolor sit amet, consectetur<br>adipiscing elit.</p></div>

  <div class="toc-num" style="left:20px;top:173px">05</div><div class="toc-bar" style="left:41px;top:170px"></div>
  <div class="toc-item" style="left:51px;top:165px"><h3>LOREM IPSUM DOLOR</h3><p>Lorem ipsum dolor sit amet, consectetur<br>adipiscing elit.</p></div>
  <div class="toc-num" style="left:204px;top:173px">06</div><div class="toc-bar" style="left:225px;top:170px"></div>
  <div class="toc-item" style="left:235px;top:165px"><h3 class="blue">LOREM IPSUM DOLOR</h3><p>Lorem ipsum dolor sit amet, consectetur<br>adipiscing elit.</p></div>
</section>

<!-- Table of contents 2 -->
<section class="slide col-r row-2">
  <div class="tab"></div>
  <h2 class="title">TABLE OF <span class="accent">CONTENTS</span></h2>
  <div class="brand top"><span class="dot"></span>SUMMIT DECK</div>

  <div class="icon-box" style="left:33px;top:62px"><svg width="15" height="15" viewBox="0 0 15 15" fill="none" stroke="var(--purple)" stroke-width=".8"><rect x="1" y="9" width="2.5" height="5"/><rect x="5" y="7" width="2.5" height="7"/><rect x="9" y="5" width="2.5" height="9"/><circle cx="12" cy="3" r="2"/></svg></div>
  <div class="toc-item" style="left:65px;top:59px"><h3>LOREM IPSUM DOLOR</h3><p>Lorem ipsum dolor sit amet, consectetur<br>adipiscing elit.</p></div>
  <div class="icon-box" style="left:210px;top:62px"><svg width="15" height="15" viewBox="0 0 15 15" fill="none" stroke="var(--blue)" stroke-width=".8"><circle cx="7.5" cy="7.5" r="3.5"/><path d="M7.5 1v2M7.5 12v2M1 7.5h2M12 7.5h2M3 3l1.4 1.4M10.6 10.6L12 12M3 12l1.4-1.4M10.6 4.4L12 3"/></svg></div>
  <div class="toc-item" style="left:242px;top:59px"><h3 class="blue">LOREM IPSUM DOLOR</h3><p>Lorem ipsum dolor sit amet, consectetur<br>adipiscing elit.</p></div>

  <div class="icon-box" style="left:33px;top:111px"><svg width="15" height="15" viewBox="0 0 15 15" fill="none" stroke="var(--purple)" stroke-width=".8"><path d="M1 13h13M3 13l3-6 3 3 4-7"/><circle cx="13" cy="3" r="1.2"/></svg></div>
  <div class="toc-item" style="left:65px;top:108px"><h3>LOREM IPSUM DOLOR</h3><p>Lorem ipsum dolor sit amet, consectetur<br>adipiscing elit.</p></div>
  <div class="icon-box" style="left:210px;top:111px"><svg width="15" height="15" viewBox="0 0 15 15" fill="none" stroke="var(--blue)" stroke-width=".8"><path d="M2 13h11M5 13V9M10 13V9M3 9h9M7.5 2v7"/><path d="M7.5 2l4 1.5-4 1.5"/></svg></div>
  <div class="toc-item" style="left:242px;top:108px"><h3 class="blue">LOREM IPSUM DOLOR</h3><p>Lorem ipsum dolor sit amet, consectetur<br>adipiscing elit.</p></div>

  <div class="icon-box" style="left:33px;top:160px"><svg width="15" height="15" viewBox="0 0 15 15" fill="none" stroke="var(--purple)" stroke-width=".8"><path d="M2 2l3 3M13 2l-3 3M2 13l3-3M13 13l-3-3"/><rect x="5" y="5" width="5" height="5"/></svg></div>
  <div class="toc-item" style="left:65px;top:157px"><h3>LOREM IPSUM DOLOR</h3><p>Lorem ipsum dolor sit amet, consectetur<br>adipiscing elit.</p></div>
  <div class="icon-box" style="left:210px;top:160px"><svg width="15" height="15" viewBox="0 0 15 15" fill="none" stroke="var(--blue)" stroke-width=".8"><path d="M1 14V10h4v4M5 14V7h4v7M9 14V4h4v10M1 14h13"/><path d="M11 1l.6 1.2 1.3.2-1 .9.3 1.3-1.2-.7-1.2.7.3-1.3-1-.9 1.3-.2z"/></svg></div>
  <div class="toc-item" style="left:242px;top:157px"><h3 class="blue">LOREM IPSUM DOLOR</h3><p>Lorem ipsum dolor sit amet, consectetur<br>adipiscing elit.</p></div>
</section>

<!-- Content slide: three columns -->
<section class="slide col-l row-3">
  <h2 class="title">CONTENT <span class="accent">SLIDE</span></h2>
  <div class="rule"></div>
  <div class="brand top"><span class="dot"></span>SUMMIT DECK</div>
  <p class="body-copy" style="left:21px;top:63px;width:96px">Lorem ipsum dolor sit amet, consectetur adipiscing elit, sed do eiusmod tempor incididunt ut labore et dolore magna aliqua. Ut enim ad minim veniam, quis nostrud exercitation ullamco laboris nisi ut aliquip ex ea commodo consequat. Duis aute irure dolor in reprehenderit in voluptate velit esse cillum dolore eu fugiat nulla pariatur. Excepteur sint occaecat cupidatat non proident, sunt in culpa qui officia.</p>
  <p class="body-copy" style="left:141px;top:63px;width:96px">Lorem ipsum dolor sit amet, consectetur adipiscing elit, sed do eiusmod tempor incididunt ut labore et dolore magna aliqua. Ut enim ad minim veniam, quis nostrud exercitation ullamco laboris nisi ut aliquip ex ea commodo consequat. Duis aute irure dolor in reprehenderit in voluptate velit esse cillum dolore eu fugiat nulla pariatur. Excepteur sint occaecat cupidatat non proident, sunt in culpa qui officia.</p>
  <p class="body-copy" style="left:261px;top:63px;width:96px">Lorem ipsum dolor sit amet, consectetur adipiscing elit, sed do eiusmod tempor incididunt ut labore et dolore magna aliqua. Ut enim ad minim veniam, quis nostrud exercitation ullamco laboris nisi ut aliquip ex ea commodo consequat. Duis aute irure dolor in reprehenderit in voluptate velit esse cillum dolore eu fugiat nulla pariatur. Excepteur sint occaecat cupidatat non proident, sunt in culpa qui officia.</p>
</section>

<!-- Content slide: single block -->
<section class="slide col-r row-3">
  <div class="tab"></div>
  <h2 class="title">CONTENT <span class="accent">SLIDE</span></h2>
  <div class="brand top"><span class="dot"></span>SUMMIT DECK</div>
  <p class="body-copy" style="left:26px;top:57px;width:330px">Lorem ipsum dolor sit amet, consectetur adipiscing elit, sed do eiusmod tempor incididunt ut labore et dolore magna aliqua. Ut enim ad minim veniam, quis nostrud exercitation ullamco laboris nisi ut aliquip ex ea commodo consequat. Duis aute irure dolor in reprehenderit in voluptate velit esse cillum dolore eu fugiat nulla pariatur. Excepteur sint occaecat cupidatat non proident, sunt in culpa qui officia deserunt mollit anim id est laborum. Sed ut perspiciatis unde omnis iste natus error sit voluptatem accusantium doloremque laudantium, totam rem aperiam, eaque ipsa quae ab illo inventore veritatis et quasi architecto beatae vitae dicta sunt explicabo. Nemo enim ipsam voluptatem quia voluptas sit aspernatur aut odit aut fugit, sed quia consequuntur magni dolores eos qui ratione voluptatem sequi nesciunt. Neque porro quisquam est, qui dolorem ipsum quia dolor sit amet, consectetur, adipisci velit, sed quia non numquam eius modi tempora incidunt ut labore et dolore magnam aliquam quaerat voluptatem. Ut enim ad minima veniam, quis nostrum exercitationem ullam corporis suscipit laboriosam, nisi ut aliquid ex ea commodi consequatur? Quis autem vel eum iure reprehenderit qui in ea voluptate velit esse quam nihil molestiae consequatur, vel illum qui dolorem eum fugiat quo voluptas nulla pariatur. Lorem ipsum dolor sit amet, consectetur adipiscing elit, sed do eiusmod tempor incididunt ut labore et dolore magna aliqua. Ut enim ad minim veniam, quis nostrud exercitation ullamco laboris nisi ut aliquip ex ea commodo consequat.</p>
</section>

<!-- Text and picture -->
<section class="slide col-l row-4">
  <h2 class="title">TEXT AND PICTURE <span class="accent">SLIDE</span></h2>
  <div class="rule"></div>
  <div class="brand top"><span class="dot"></span>SUMMIT DECK</div>
  <p class="body-copy" style="left:21px;top:58px;width:160px">Lorem ipsum dolor sit amet, consectetur adipiscing elit, sed do eiusmod tempor incididunt ut labore et dolore magna aliqua. Ut enim ad minim veniam, quis nostrud exercitation ullamco laboris nisi ut aliquip ex ea commodo consequat. Duis aute irure dolor in reprehenderit in voluptate velit esse cillum dolore eu fugiat nulla pariatur. Excepteur sint occaecat cupidatat non proident, sunt in culpa qui officia deserunt mollit anim id est laborum. Sed ut perspiciatis unde omnis iste natus<br>error sit voluptatem accusantium<br>doloremque laudantium.</p>
  <div class="photo" role="img" aria-label="Photo: many hands joining white puzzle pieces in a circle" style="left:196px;top:53px;width:179px;height:158px;background:radial-gradient(circle at 50% 50%,#f2f2f2 0%,#e3d2c6 45%,#c9a58c 75%,#5a5a5a 100%)"></div>
  <div class="callout"><h4>HAPPY CLIENTS</h4><p>Lorem ipsum dolor sit amet,<br>consectetur adipiscing</p></div>
</section>

<!-- Data driven chart -->
<section class="slide col-r row-4">
  <div class="tab"></div>
  <h2 class="title" style="left:26px">DATA DRIVEN <span class="accent">CHART</span></h2>
  <div class="brand top"><span class="dot"></span>SUMMIT DECK</div>
  <p class="body-copy" style="left:26px;top:52px;width:118px">Lorem ipsum dolor sit amet, consectetur adipiscing elit, sed do eiusmod tempor incididunt ut labore et dolore magna aliqua. Ut enim ad minim veniam, quis nostrud exercitation ullamco laboris nisi ut aliquip ex ea commodo consequat. Duis aute irure dolor in reprehenderit in voluptate velit esse cillum dolore eu fugiat nulla pariatur. Excepteur sint occaecat cupidatat non proident.</p>
  <div class="legend" style="top:97px;background:var(--purple)"></div>
  <div class="legend" style="top:117px;background:var(--blue)"></div>
  <div class="legend" style="top:138px;background:var(--green)"></div>
  <svg class="photo" style="left:170px;top:59px" width="164" height="112" viewBox="0 0 164 112" role="img" aria-label="Bar chart of three series from 2021 to 2024">
    <rect x="1" y="1" width="162" height="110" rx="3" fill="#fff" stroke="#111" stroke-width="2.5"/>
    <g font-family="Poppins,sans-serif" font-size="5" fill="#222">
      <text x="8" y="17">6</text><text x="8" y="29">5</text><text x="8" y="41">4</text><text x="8" y="54">3</text><text x="8" y="66">2</text><text x="8" y="78">1</text><text x="8" y="90">0</text>
      <text x="32" y="102">2021</text><text x="64" y="102">2022</text><text x="95" y="102">2023</text><text x="128" y="102">2024</text>
    </g>
    <g stroke="#ddd" stroke-width=".4"><path d="M16 15h140M16 27h140M16 39h140M16 52h140M16 64h140M16 76h140M16 88h140"/></g>
    <g>
      <rect x="30" y="36" width="3" height="52" fill="var(--purple)"/><rect x="37" y="59" width="3" height="29" fill="var(--blue)"/><rect x="43" y="65" width="3" height="23" fill="var(--green)"/>
      <rect x="62" y="58" width="3" height="30" fill="var(--purple)"/><rect x="69" y="34" width="3" height="54" fill="var(--blue)"/><rect x="75" y="65" width="3" height="23" fill="var(--green)"/>
      <rect x="93" y="47" width="3" height="41" fill="var(--purple)"/><rect x="100" y="68" width="3" height="20" fill="var(--blue)"/><rect x="106" y="52" width="3" height="36" fill="var(--green)"/>
      <rect x="125" y="36" width="3" height="52" fill="var(--purple)"/><rect x="132" y="56" width="3" height="32" fill="var(--blue)"/><rect x="138" y="28" width="3" height="60" fill="var(--green)"/>
    </g>
  </svg>
</section>

<!-- Section header with photo -->
<section class="slide col-l row-5">
  <div class="photo" role="img" aria-label="Photo: climbers helping each other up a rock cliff against a cloudy sky" style="inset:0;background:linear-gradient(100deg,#6d87a4 0%,#a9bccd 45%,#5b554f 75%,#2f2a26 100%)"></div>
  <h2 class="title light">SECTION HEADER <span class="accent">SLIDE</span></h2>
  <div class="rule light"></div>
  <div class="brand top light"><span class="dot"></span>SUMMIT DECK</div>
</section>

<!-- Section header plain -->
<section class="slide col-r row-5">
  <div class="tab"></div>
  <h2 class="title" style="left:26px">SECTION HEADER <span class="accent">SLIDE</span></h2>
  <div class="brand top"><span class="dot"></span>SUMMIT DECK</div>
</section>

</body>
</html>
```